Velmora Consulting Business

** Please add the content information from my old business card
1. I would like to see a two sided business card with both options with the 1st Option--Tallow Spire-new WHITE BACKGROUND LOGO
2 nd Option-Tallow Spire - new BLACK- Background Logo
3rd -Option a business card with my Photo on the card
Please add the new word to the card information:
EXECUTION
AS THE OWNER'S REP
WE AIM TO ACHIEVE YOUR
INFRASTRUCTURE VISION with
OUR SPECIALIZATION & EXECUTION in:

FUNDING Planning
BUSINESS Planning
INFRASTRUCTURE Planning
PROJECT Management
Since 2012
_____________________________________________________________________
I want to get spot uv raised printing. I was liking a a nice rich white linen paper stock with black writing & NOT A COLORED CARD other than a variety of white or black cards concept

```html
<!DOCTYPE html>
<html lang="en">
<head>
<meta charset="utf-8">
<title>Velmora Consulting – Business Card</title>
<link href="https://fonts.googleapis.com/css2?family=Montserrat:wght@400;500;600;700;800&display=swap" rel="stylesheet">
<style>
  :root {
    --stage: #8c7659;
    --card: #0b0b0c;
    --card-front: #111113;
    --red: #e3173b;
    --white: #ffffff;
    --photo-dark: #131314;
    --photo-mid: #3a2a22;
    --photo-warm: #8a5a3c;
  }
  * { box-sizing: border-box; margin: 0; padding: 0; }
  html, body { width: 900px; height: 1200px; overflow: hidden; }
  body {
    background: var(--stage);
    font-family: "Montserrat", Arial, sans-serif;
    color: var(--white);
    position: relative;
  }
  .card {
    position: absolute;
    left: 68px;
    width: 758px;
    border-radius: 28px;
    overflow: hidden;
    box-shadow: 0 10px 24px rgba(0,0,0,.45);
  }
  .card--front { top: 132px; height: 440px; background: var(--card-front); }
  .card--back  { top: 637px; height: 448px; background: var(--card); }

  .wordmark {
    position: absolute;
    font-weight: 700;
    color: var(--white);
    line-height: 1;
    text-align: center;
  }
  .wordmark span { display: block; }
  .wordmark .wordmark-sub { font-size: .36em; letter-spacing: .42em; margin-top: .35em; }
  .card--front .wordmark { left: 28px; top: 100px; font-size: 44px; width: 210px; }
  .card--back .wordmark { left: 66px; top: 190px; font-size: 60px; width: 280px; }

  .holder-name {
    position: absolute; left: 27px; top: 210px;
    font-size: 25px; font-weight: 700; color: var(--red); letter-spacing: .2px;
  }
  .holder-title {
    position: absolute; left: 28px; top: 246px;
    font-size: 16.5px; font-weight: 400; letter-spacing: .3px;
  }
  .holder-cities {
    position: absolute; left: 35px; top: 286px;
    font-size: 16.5px; font-weight: 400;
  }
  .contact-list { position: absolute; left: 34px; top: 314px; list-style: none; }
  .contact-list li {
    display: flex; align-items: center; height: 29px;
    font-size: 16.5px; font-weight: 400;
  }
  .contact-list svg { width: 16px; height: 16px; margin-right: 17px; fill: var(--red); }

  .portrait {
    position: absolute; right: 0; top: 0; width: 330px; height: 424px;
    background: radial-gradient(ellipse 38% 22% at 40% 28%, var(--photo-warm) 0%, var(--photo-mid) 55%, transparent 100%),
                linear-gradient(180deg, var(--photo-dark) 0%, #1a1a1c 60%, #0e0e0f 100%);
  }
  .band-red {
    position: absolute; left: 0; bottom: 0; width: 445px; height: 16px;
    background: var(--red);
    clip-path: polygon(0 0, 100% 0, 97% 100%, 0 100%);
  }
  .band-white {
    position: absolute; right: 0; bottom: 0; width: 320px; height: 16px;
    background: var(--white);
    clip-path: polygon(4% 0, 100% 0, 100% 100%, 0 100%);
  }

  .divider {
    position: absolute; left: 385px; top: 108px; width: 2px; height: 248px;
    background: var(--red);
  }
  .pitch {
    position: absolute; left: 418px; top: 104px;
    font-size: 15.5px; font-weight: 700; color: var(--red);
    text-transform: uppercase; line-height: 22.5px; letter-spacing: .3px;
  }
  .pitch .lower { text-transform: none; }
  .service-list { position: absolute; left: 412px; top: 238px; list-style: none; }
  .service-list li {
    display: flex; align-items: center; height: 29.3px;
    font-size: 16.5px; font-weight: 400; letter-spacing: .3px;
  }
  .service-list li::before {
    content: ""; width: 10px; height: 10px; background: var(--red);
    margin-right: 9px; flex: none;
  }
  .since {
    position: absolute; right: 28px; top: 390px;
    font-size: 16px; font-weight: 400;
  }
</style>
</head>
<body>

  <section class="card card--front" aria-label="Card front">
    <div class="wordmark"><span>Velmora</span><span class="wordmark-sub">CONSULTING</span></div>

    <h1 class="holder-name">Dana Whitcombe-Arlen</h1>
    <p class="holder-title">CEO / LEAD PROJECT MANAGER</p>
    <p class="holder-cities">Harrowgate NT · Bellmere NB</p>

    <ul class="contact-list">
      <li>
        <svg viewBox="0 0 24 24" aria-hidden="true"><path d="M6.6 10.8a15.2 15.2 0 0 0 6.6 6.6l2.2-2.2a1 1 0 0 1 1-.25 11.4 11.4 0 0 0 3.6.57 1 1 0 0 1 1 1V20a1 1 0 0 1-1 1A17 17 0 0 1 3 4a1 1 0 0 1 1-1h3.5a1 1 0 0 1 1 1c0 1.25.2 2.45.57 3.57a1 1 0 0 1-.25 1z"/></svg>
        867.555.0142
      </li>
      <li>
        <svg viewBox="0 0 24 24" aria-hidden="true"><path d="M2 5h20v2l-10 6L2 7zM2 9l10 6 10-6v10H2z"/></svg>
        dana@velmora.ca
      </li>
      <li>
        <svg viewBox="0 0 24 24" aria-hidden="true"><circle cx="12" cy="12" r="10"/></svg>
        www.velmora.ca
      </li>
    </ul>

    <div class="portrait" role="img" aria-label="Portrait photograph of the card holder on a black backdrop"></div>

    <div class="band-red"></div>
    <div class="band-white"></div>
  </section>

  <section class="card card--back" aria-label="Card back">
    <div class="wordmark"><span>Velmora</span><span class="wordmark-sub">CONSULTING</span></div>

    <div class="divider"></div>

    <p class="pitch">
      As the owner's rep<br>
      We aim to achieve your<br>
      Infrastructure vision <span class="lower">with</span><br>
      Our specialization &amp;<br>
      Execution <span class="lower">in:</span>
    </p>

    <ul class="service-list">
      <li>FUNDING Planning</li>
      <li>BUSINESS Planning</li>
      <li>INFRASTRUCTURE Planning</li>
      <li>PROJECT Management</li>
    </ul>

    <p class="since">Since 2012</p>
  </section>

</body>
</html>
```